Association qui souhaite améliorer l'accès aux personnes en situation de handicap

Nous sommes une association qui a pour objectif d'améliorer l'accessibilité, augmenter l'offre des activités réalisables dans notre région touristique.
Nous souhaitons réaliser un site internet afin de pouvoir communiquer sur notre association. Nous avons déjà conçu notre flyer sur Plumotrix. Nous souhaiterions une base graphique se rapportant à celui-ci. C'est possible de tout retravailler mais nous souhaitons tout de même retrouver la charte graphique ou code couleur du flyer.
Il nous faudrait quelques pages:
- 1 page : Acceuil / Présentation (Home), Il y aurait le descriptif de l'association, avec ses objectifs à +/- moyen terme
- 1 page : Nos réalisations, celle-ci présenterait les éléments que nous avons réalisés avec des zones de textes et des images classées chronologiquement au fur et à mesure des nouveautés
- 1 page : Media, comme la précédente, mais ou on pourrait voir ou lire sur les divers médias qui parlent de nous
- 1 page : Evenements : c'est une page pour présenter divers activités que nous allons organiser
- 1 page : Contact qui indique comment nous contacter et avec la présentation des 5 ou 6 membres du comité
- 1 link donate : qui arrive sur un formulaire de donnée que l'on pourra faire évoluer sur un système de payement par la suite. Cette bannière doit se retrouver sur toutes les pages
Il est nécessaire que se design puisse être transféré sur une lecture sur téléphone mobile
Personnes en situation de handicap
Associatif

```html
<!DOCTYPE html>
<html lang="en">
<head>
<meta charset="utf-8">
<title>Open Paths Association</title>
<link href="https://fonts.googleapis.com/css2?family=Raleway:wght@400;500;600;700;800&family=Open+Sans:wght@400;600;700&display=swap" rel="stylesheet">
<style>
:root{
  --red:#c4122f;
  --red-dark:#a10d25;
  --ink:#222222;
  --text:#555555;
  --muted:#888888;
  --light:#f5f5f5;
  --dark:#262626;
  --darker:#1c1c1c;
  --white:#ffffff;
}
*{box-sizing:border-box;margin:0;padding:0}
html,body{width:1200px;height:3332px;overflow:hidden;background:var(--white)}
body{font-family:"Open Sans",Arial,sans-serif;color:var(--text);position:relative}
h1,h2,h3,h4,.nav,.btn,.brand{font-family:"Raleway",Arial,sans-serif}
.btn{display:inline-block;background:var(--red);color:var(--white);font-size:11px;font-weight:700;letter-spacing:.5px;padding:12px 26px;border-radius:22px;text-transform:uppercase}
.fill{position:absolute}

/* top bar */
.topbar{height:24px;background:var(--red);display:flex;align-items:center;justify-content:space-between;padding:0 130px;color:var(--white);font-size:10px}
.topbar .social{display:flex;gap:10px}
.dot{width:10px;height:10px;border-radius:50%;background:var(--white);display:inline-block}
.topbar .contact{display:flex;gap:18px;align-items:center}
.topbar .contact span{display:flex;align-items:center;gap:5px}

/* header */
.header{height:70px;display:flex;align-items:center;justify-content:space-between;padding:0 130px;border-bottom:1px solid #eee}
.brand{display:flex;align-items:center;gap:8px;color:var(--red);font-weight:800;font-size:13px;line-height:1.1;text-transform:uppercase}
.brand .mark{width:22px;height:22px;background:var(--red)}
.nav{display:flex;align-items:center;gap:36px;font-size:12px;font-weight:600;color:var(--ink)}
.nav .active{color:var(--red);border-bottom:2px solid var(--red);padding-bottom:3px}

/* hero */
.hero{position:relative;height:310px}
.hero-text{position:absolute;left:130px;top:110px;width:420px}
.hero-text h4{font-size:20px;font-weight:700;color:var(--ink);text-transform:uppercase}
.hero-text h1{font-size:38px;font-weight:800;color:var(--ink);text-transform:uppercase;line-height:1.1}
.hero-text h1 em{font-style:normal;color:var(--red)}
.hero-text p{font-size:12px;margin:10px 0 26px;line-height:1.6}
.hero-photo{left:612px;top:0;width:508px;height:310px;background:linear-gradient(160deg,#dfe6ea,#9fb1bd 55%,#6e6560)}

/* welcome */
.welcome{position:relative;height:440px;margin-top:180px}
.welcome-photo{left:130px;top:0;width:458px;height:362px;background:linear-gradient(140deg,#8fb04a,#4f7a2a 60%,#c9c3a8)}
.welcome-text{position:absolute;left:608px;top:30px;width:460px}
.welcome-text h4{font-size:12px;font-weight:700;color:var(--ink);text-transform:uppercase}
.welcome-text h2{font-size:32px;font-weight:500;color:var(--ink);margin:4px 0 16px}
.welcome-text h2 b{color:var(--red);font-weight:700}
.welcome-text p{font-size:11px;line-height:1.75;margin-bottom:20px}

/* achievements */
.achievements{position:relative;height:508px;margin-top:-48px;overflow:hidden}
.achievements-bg{left:0;top:0;width:1200px;height:508px;background:linear-gradient(120deg,#2b2b2b,#3c3a34 50%,#444)}
.achievements .slant{position:absolute;left:0;top:0}
.achievements-text{position:absolute;left:130px;top:128px;width:420px;color:#ddd}
.achievements-text h2{font-size:32px;font-weight:500;color:var(--white);margin-bottom:18px}
.achievements-text p{font-size:11px;line-height:1.7;margin-bottom:28px}

/* media */
.media{position:relative;height:368px;text-align:center;padding-top:58px}
.section-title{font-size:32px;font-weight:600;color:var(--ink)}
.section-sub{font-size:11px;color:var(--muted);margin-top:4px}
.media-grid{display:flex;gap:22px;justify-content:center;margin-top:24px}
.media-card{width:300px;height:180px;position:relative}
.media-card .img{width:100%;height:100%}
.media-card .caption{position:absolute;left:50%;bottom:12px;transform:translateX(-50%);background:var(--white);font-size:10px;font-weight:600;color:var(--ink);padding:6px 14px;white-space:nowrap;display:flex;gap:6px;align-items:center}
.media-card .caption i{color:var(--red);font-style:normal}

/* events */
.events{position:relative;height:620px}
.events-bg{left:0;top:0;width:1200px;height:620px;background:linear-gradient(180deg,#2d2d2d,#222 60%,#333)}
.events-inner{position:absolute;left:130px;top:60px;width:940px;text-align:center}
.events-inner .section-title{color:var(--white)}
.event-grid{display:flex;gap:22px;margin-top:22px}
.event-card{width:298px;height:416px;background:var(--white);text-align:left;position:relative}
.event-card .img{height:212px}
.event-card .date{position:absolute;left:14px;top:0;width:32px;height:48px;background:var(--red);color:var(--white);font-size:9px;font-weight:700;text-align:center;padding-top:8px;line-height:1.3}
.event-card .body{padding:20px 22px}
.event-card h3{font-size:17px;font-weight:700;color:var(--ink);margin-bottom:8px}
.event-card p{font-size:10.5px;line-height:1.6;margin-bottom:18px}

/* contact */
.contact{position:relative;height:380px}
.contact-photo{left:130px;top:20px;width:310px;height:338px;background:linear-gradient(150deg,#a9b7c0,#6f8a52 45%,#b1343a 80%)}
.contact-form{position:absolute;left:608px;top:40px;width:462px}
.contact-form h2{font-size:32px;font-weight:500;color:var(--ink)}
.contact-form .lead{font-size:11px;color:var(--muted);margin:2px 0 20px}
.form{display:grid;grid-template-columns:1fr 1fr;gap:10px}
.field{border:1px solid #ccc;height:26px;font-size:9px;color:var(--muted);padding:6px 8px}
.field.area{grid-row:1 / span 3;grid-column:2;height:82px}
.submit{grid-column:2;background:var(--red);color:var(--white);font-size:9px;font-weight:700;text-align:center;height:24px;line-height:24px;text-transform:uppercase}

/* footer */
.footer{position:absolute;left:0;top:2980px;width:1200px;height:352px;background:var(--darker);color:#bbb}
.footer-cols{position:absolute;left:130px;top:60px;width:940px;display:flex}
.fcol{width:235px;font-size:10px;line-height:2}
.fcol h4{color:var(--red);font-size:12px;font-weight:700;text-transform:uppercase;margin-bottom:10px}
.fcol .brand{margin-bottom:12px}
.fcol .brand span{color:var(--white)}
.fcol p{line-height:1.6;width:190px}
.footer .social{display:flex;gap:10px;margin-top:14px}
.footer .social .dot{width:18px;height:18px;background:var(--red)}
.contact-line{display:flex;align-items:center;gap:8px}
.copyright{position:absolute;left:0;right:0;bottom:26px;text-align:center;font-size:9px;color:#999}
.copyright b{color:var(--red);font-weight:600}
</style>
</head>
<body>

<div class="topbar">
  <div class="social"><span class="dot"></span><span class="dot"></span></div>
  <div class="contact">
    <span><svg width="10" height="10" viewBox="0 0 24 24"><path fill="#fff" d="M6.6 10.8a15 15 0 0 0 6.6 6.6l2.2-2.2c.3-.3.7-.4 1-.2 1.1.4 2.3.6 3.6.6.6 0 1 .4 1 1V20c0 .6-.4 1-1 1A17 17 0 0 1 3 4c0-.6.4-1 1-1h3.5c.6 0 1 .4 1 1 0 1.3.2 2.5.6 3.6.1.3 0 .7-.2 1z"/></svg>+1 (555) 246 8100</span>
    <span><svg width="11" height="9" viewBox="0 0 24 18"><rect x="1" y="1" width="22" height="16" fill="none" stroke="#fff" stroke-width="2"/><path d="M1 1l11 9 11-9" fill="none" stroke="#fff" stroke-width="2"/></svg>info@openpathsassoc.org</span>
  </div>
</div>

<header class="header">
  <div class="brand"><span class="mark"></span><span>Open Paths<br>Association</span></div>
  <nav class="nav">
    <span class="active">Home</span><span>Our Achievements</span><span>Media</span><span>Events</span><span>Contact</span>
    <span class="btn" style="padding:8px 22px">Donate</span>
  </nav>
</header>

<section class="hero">
  <div class="fill hero-photo" role="img" aria-label="Photo of two smiling wheelchair users outside a modern glass-domed building"></div>
  <div class="hero-text">
    <h4>Access the</h4>
    <h1><em style="color:var(--ink)">Tourist</em> <em>Region</em></h1>
    <p>The resources of the association come from subscriptions, donations and events organized throughout the year.</p>
    <span class="btn">Read more</span>
  </div>
</section>

<section class="welcome">
  <div class="fill welcome-photo" role="img" aria-label="Photo of a man walking with a cane along a sunny garden path"></div>
  <div class="welcome-text">
    <h4>Welcome to</h4>
    <h2>Open <b>Paths</b> Association</h2>
    <p>Sed ut perspiciatis unde omnis iste natus error sit voluptatem accusantium doloremque laudantium, totam rem aperiam, eaque ipsa quae ab illo inventore veritatis et quasi architecto beatae vitae dicta sunt explicabo. Nemo enim ipsam voluptatem quia voluptas sit aspernatur aut odit aut fugit, sed quia consequuntur magni dolores eos qui ratione voluptatem sequi nesciunt.</p>
    <span class="btn">Read more</span>
  </div>
</section>

<section class="achievements">
  <div class="fill achievements-bg" role="img" aria-label="Darkened background photo of a person in a wheelchair outdoors"></div>
  <svg class="slant" width="1200" height="508" viewBox="0 0 1200 508">
    <polygon points="760,0 1200,0 1200,508 560,508" fill="#ffffff"/>
    <polygon points="786,0 1200,0 1200,508 588,508" fill="#8a7a6e" role="img" aria-label="Close-up photo of a hand resting on a wheelchair wheel"/>
  </svg>
  <div class="achievements-text">
    <h2>Our Achievements</h2>
    <p>Sed ut perspiciatis unde omnis iste natus error sit voluptatem accusantium doloremque laudantium, totam rem aperiam, eaque ipsa quae ab illo inventore veritatis et quasi architecto beatae vitae dicta sunt explicabo. Nemo enim ipsam voluptatem quia voluptas sit aspernatur aut odit aut fugit, sed quia consequuntur magni dolores eos qui ratione voluptatem.</p>
    <span class="btn">Read more</span>
  </div>
</section>

<section class="media">
  <h2 class="section-title">Our Media</h2>
  <p class="section-sub">Sed ut perspiciatis unde omnis iste natus error sit voluptatem</p>
  <div class="media-grid">
    <div class="media-card"><div class="img" role="img" aria-label="Photo of a volunteer helping a child in a wheelchair outdoors" style="background:linear-gradient(150deg,#7fa0b8,#5c7a4a)"></div><div class="caption">Voluptas Sit Aspernatur <i>&rarr;</i></div></div>
    <div class="media-card"><div class="img" role="img" aria-label="Photo of people helping a wheelchair user on a snowy path" style="background:linear-gradient(150deg,#e8ecef,#b6bcc2 60%,#6b6f73)"></div><div class="caption">Voluptas Sit Aspernatur <i>&rarr;</i></div></div>
    <div class="media-card"><div class="img" role="img" aria-label="Photo of a caregiver with an elderly person in a wheelchair indoors" style="background:linear-gradient(150deg,#d9cfc0,#a89480 60%,#6e7d99)"></div><div class="caption">Voluptas Sit Aspernatur <i>&rarr;</i></div></div>
  </div>
</section>

<section class="events">
  <div class="fill events-bg" role="img" aria-label="Darkened background photo of a group activity"></div>
  <div class="events-inner">
    <h2 class="section-title">Recent Event</h2>
    <div class="event-grid">
      <div class="event-card"><div class="img" role="img" aria-label="Photo of a young child drinking from a cup outdoors" style="background:linear-gradient(150deg,#8aa35a,#6a5a9a)"></div><div class="date">24<br>MAY</div><div class="body"><h3>Neque Porro Wuisquam</h3><p>Sed ut perspiciatis unde omnis iste natus error sit voluptatem accusantium doloremque.</p><span class="btn">Read more</span></div></div>
      <div class="event-card"><div class="img" role="img" aria-label="Photo of a group of people around a table at an outdoor activity" style="background:linear-gradient(150deg,#c9c3b5,#7c8a6a 60%,#4b5a6e)"></div><div class="date">24<br>MAY</div><div class="body"><h3>Neque Porro Wuisquam</h3><p>Sed ut perspiciatis unde omnis iste natus error sit voluptatem accusantium doloremque.</p><span class="btn">Read more</span></div></div>
      <div class="event-card"><div class="img" role="img" aria-label="Photo of a wheelchair sports team on a court" style="background:linear-gradient(150deg,#9cb6d2,#3b5fa0 55%,#7a8a5a)"></div><div class="date">24<br>MAY</div><div class="body"><h3>Neque Porro Wuisquam</h3><p>Sed ut perspiciatis unde omnis iste natus error sit voluptatem accusantium doloremque.</p><span class="btn">Read more</span></div></div>
    </div>
  </div>
</section>

<section class="contact">
  <div class="fill contact-photo" role="img" aria-label="Photo of a person in a red jacket riding an adapted cycle outdoors"></div>
  <div class="contact-form">
    <h2>Contact Us</h2>
    <p class="lead">Sed ut perspiciatis unde omnis iste natus error.</p>
    <div class="form">
      <div class="field">Name</div>
      <div class="field area">Comments</div>
      <div class="field">Email</div>
      <div class="field">Phone</div>
      <div class="submit">Submit</div>
    </div>
  </div>
</section>

<footer class="footer">
  <div class="footer-cols">
    <div class="fcol">
      <div class="brand"><span class="mark"></span><span>Open Paths<br>Association</span></div>
      <p>Sed ut perspiciatis unde omnis iste natus error sit voluptatem accusantium doloremque laudantium.</p>
      <div class="social"><span class="dot"></span><span class="dot"></span></div>
    </div>
    <div class="fcol">
      <h4>Sitemap</h4>
      <div>Home</div><div>Our Achievements</div><div>Media</div><div>Events</div><div>Contact Us</div>
    </div>
    <div class="fcol">
      <h4>Others</h4>
      <div>Privacy Policy</div><div>Terms &amp; Conditions</div><div>Legal</div><div>Donate</div><div>Help / Support</div>
    </div>
    <div class="fcol">
      <h4>Contacts</h4>
      <div class="contact-line"><svg width="10" height="12" viewBox="0 0 20 24"><path fill="#c4122f" d="M10 0a8 8 0 0 0-8 8c0 6 8 16 8 16s8-10 8-16a8 8 0 0 0-8-8zm0 11a3 3 0 1 1 0-6 3 3 0 0 1 0 6z"/></svg>Grand Rue 12, 1000 Valmont</div>
      <div class="contact-line"><svg width="10" height="10" viewBox="0 0 24 24"><path fill="#c4122f" d="M6.6 10.8a15 15 0 0 0 6.6 6.6l2.2-2.2c.3-.3.7-.4 1-.2 1.1.4 2.3.6 3.6.6.6 0 1 .4 1 1V20c0 .6-.4 1-1 1A17 17 0 0 1 3 4c0-.6.4-1 1-1h3.5c.6 0 1 .4 1 1 0 1.3.2 2.5.6 3.6.1.3 0 .7-.2 1z"/></svg>+1 (555) 246 8100</div>
      <div class="contact-line"><svg width="11" height="9" viewBox="0 0 24 18"><rect x="1" y="1" width="22" height="16" fill="none" stroke="#c4122f" stroke-width="2"/><path d="M1 1l11 9 11-9" fill="none" stroke="#c4122f" stroke-width="2"/></svg>info@openpathsassoc.org</div>
    </div>
  </div>
  <div class="copyright">Copyright &copy; 2023 <b>Open Paths Association</b>. All Rights Reserved.</div>
</footer>

</body>
</html>
```